gtw school poster design and change logo name

We already have a logo which only needs to be slightly modified with "school".
We also have two advertising faces, a girl and a boy, which should be on our poster.
Important key data:

bilingual D/E small classes
daycare
private kindergarten
private school from 2024

Poster size: 268,5 x 128 cm
We need logo sizes in different sizes
also for T-shirts.
Attached also a old poster

new clients

0094D4
00A9DD
6FCCEA
C7EBF8
E9F6FB
59FF00
82FF00
B8FF75
E3FFCB
F4FFEA
FFC000
F8CF3A
FAE287
FDF2CF
FEFAEE
F0912C
F2A743
F7CA91
FBE8D2
FDF5EE

```html
<!DOCTYPE html>
<html lang="de">
<head>
<meta charset="utf-8">
<title>gtw school – Banner</title>
<link rel="stylesheet" href="https://fonts.googleapis.com/css2?family=Fredoka:wght@400;500;600;700&family=Poppins:wght@600;700&display=swap">
<style>
  :root {
    --blue: #00A9DD;
    --pink: #EC4A9C;
    --orange: #FFAA00;
    --orange-text: #F8A81E;
    --green: #A8CC12;
    --ink: #1E1E1E;
    --white: #FFFFFF;
    --stage: #E4E3E3;
  }
  * { margin: 0; padding: 0; box-sizing: border-box; }
  html, body { width: 1200px; height: 671px; overflow: hidden; background: var(--stage); }
  .banner {
    position: absolute; left: 20px; top: 59px; width: 1160px; height: 553px;
    background: var(--white); overflow: hidden;
    font-family: "Fredoka", "Arial Rounded MT Bold", sans-serif;
  }
  .layer { position: absolute; left: 0; top: 0; }
  .brand {
    position: absolute; left: 44px; top: 82px;
    display: flex; align-items: center; gap: 10px;
    font-weight: 600; font-size: 32px; line-height: 1; color: var(--orange-text);
  }
  .brand-dot { width: 20px; height: 20px; border-radius: 50%; background: var(--orange-text); }
  .headline { position: absolute; left: 232px; top: 28px; line-height: 1; white-space: nowrap; }
  .headline-blue { font-size: 56px; font-weight: 700; color: var(--blue); }
  .headline-pink { font-size: 53px; font-weight: 700; color: var(--pink); margin-top: -2px; }
  .headline-orange { font-size: 41px; font-weight: 500; color: var(--orange-text); margin-top: 2px; }
  .intro {
    position: absolute; left: 38px; top: 190px; white-space: nowrap;
    font-size: 26px; font-weight: 500; line-height: 29px; color: var(--ink);
  }
  .pills { position: absolute; left: 40px; top: 258px; display: flex; }
  .pill {
    height: 36px; border-radius: 18px;
    font-size: 25px; font-weight: 500; line-height: 1; color: var(--white);
    display: flex; align-items: center; white-space: nowrap;
  }
  .pill-green { background: var(--green); position: relative; z-index: 1; width: 312px; padding-left: 14px; }
  .pill-blue { background: var(--blue); margin-left: -18px; width: 308px; padding-left: 32px; border-radius: 0 18px 18px 0; }
  .pink-band {
    position: absolute; left: 0; top: 306px; width: 640px; height: 56px;
    background: var(--pink); color: var(--white);
    display: flex; align-items: center; padding-left: 38px;
    font-size: 25px; font-weight: 500; white-space: nowrap;
  }
  .pink-band .divider { width: 2px; height: 28px; background: var(--white); margin: 0 12px; }
  .contact-row {
    position: absolute; left: 40px; display: flex; align-items: center; gap: 16px;
    font-family: "Poppins", sans-serif; color: var(--ink); white-space: nowrap;
  }
  .row-phone { top: 372px; height: 60px; }
  .row-address { top: 428px; height: 30px; }
  .phone { font-size: 54px; font-weight: 700; line-height: 1; letter-spacing: 1px; }
  .address { font-size: 19px; font-weight: 700; line-height: 1; }
  .url-band {
    position: absolute; left: 0; top: 465px; width: 610px; height: 66px;
    background: var(--orange); color: var(--white);
    font-family: "Poppins", sans-serif; font-weight: 600; font-size: 38px;
    display: flex; align-items: center; padding-left: 38px;
  }
  .speech-text {
    position: absolute; left: 681px; top: 40px; width: 200px; text-align: center;
    font-size: 37px; font-weight: 600; line-height: 35px; color: var(--white);
  }
</style>
</head>
<body>
  <div class="banner">
    <svg class="layer" width="1160" height="553" viewBox="0 0 1160 553" aria-hidden="true">
      <path d="M688 0 Q612 250 760 553 L1160 553 L1160 0 Z" fill="var(--orange)"/>
    </svg>

    <svg class="layer" width="1160" height="553" viewBox="0 0 1160 553" role="img" aria-label="Photo of a smiling girl and a laughing boy showing their paint-covered hands">
      <defs>
        <linearGradient id="childrenTones" x1="0" y1="0" x2="1" y2="0">
          <stop offset="0" stop-color="#F3CDB1"/>
          <stop offset="0.45" stop-color="#E9B48F"/>
          <stop offset="0.75" stop-color="#4FB9E0"/>
          <stop offset="1" stop-color="#2FA7D8"/>
        </linearGradient>
      </defs>
      <path d="M612 553 L612 450 Q640 400 652 330 Q680 232 765 228 Q825 226 848 190 Q880 95 990 82 L1160 92 L1160 553 Z" fill="url(#childrenTones)"/>
    </svg>

    <div class="brand"><span class="brand-dot"></span>gtw school</div>

    <div class="headline">
      <div class="headline-blue">BILINGUAL D/E</div>
      <div class="headline-pink">KLEINE KLASSEN</div>
      <div class="headline-orange">Kindertagesstätte</div>
    </div>

    <p class="intro">Bei uns lernen ALLE Kinder spielend einfach in<br>kürzester Zeit Englisch wie eine 2.Muttersprache.</p>

    <div class="pills">
      <span class="pill pill-green">Privater Kindergarten</span>
      <span class="pill pill-blue">Privatschule ab 2024</span>
    </div>

    <div class="pink-band">Kinderkrippe &amp; Hort<span class="divider"></span>Bis zum 12.Lebensjahr</div>

    <div class="contact-row row-phone">
      <svg width="32" height="32" viewBox="0 0 24 24" aria-hidden="true">
        <path d="M6.6 10.8a15 15 0 0 0 6.6 6.6l2.2-2.2a1 1 0 0 1 1-.25 11.4 11.4 0 0 0 3.6.6 1 1 0 0 1 1 1V20a1 1 0 0 1-1 1A17 17 0 0 1 3 4a1 1 0 0 1 1-1h3.5a1 1 0 0 1 1 1c0 1.25.2 2.45.6 3.6a1 1 0 0 1-.25 1z" fill="var(--blue)"/>
        <path d="M15 3a6 6 0 0 1 6 6M15 6.5A2.5 2.5 0 0 1 17.5 9" stroke="var(--blue)" stroke-width="1.6" fill="none" stroke-linecap="round"/>
      </svg>
      <span class="phone">+41 44 555 2030</span>
    </div>
    <div class="contact-row row-address">
      <svg width="32" height="30" viewBox="0 0 24 24" aria-hidden="true">
        <path d="M12 2a7 7 0 0 0-7 7c0 5 7 12 7 12s7-7 7-12a7 7 0 0 0-7-7zm0 9.5A2.5 2.5 0 1 1 12 6.5a2.5 2.5 0 0 1 0 5z" fill="var(--blue)"/>
        <ellipse cx="12" cy="22" rx="5" ry="1.2" fill="var(--blue)"/>
      </svg>
      <span class="address">Lindenweg 12, 8400 Winterthal</span>
    </div>

    <div class="url-band">www.gtw-daycare.ch</div>

    <svg class="layer" width="1160" height="553" viewBox="0 0 1160 553" aria-hidden="true">
      <ellipse cx="781" cy="98" rx="104" ry="76" fill="var(--blue)"/>
      <path d="M758 160 Q770 190 815 200 Q790 180 800 165 Z" fill="var(--blue)"/>
    </svg>
    <div class="speech-text">Do You<br>Speak<br>English ?</div>
  </div>
</body>
</html>
```